Business Card Design Project

- makeup artist business card

- original and creative

- Elegant design

- Feel free to come out with cool designs but stick to being elegant and attractive

- Design relates to makeup

- includes name, occupation, contact numbers, email, website

- regular size business card

- round corner card

- double sided

- on 1 side it should just have the website name in the center " moonveilstudio.net "

Industry/Entity Type

Business

Requirements
Must have
• Delia Marsh
Makeup Artist
USA: +1 (415)772-0461
Singapore: +65 82307915
deliamarsh@moonveilstudio.net
www.moonveilstudio.net
Should not have
• nothing cartoon looking.
Pictures of makeup being grab from the internet.. Examples: eyes or lips.

```html
<!DOCTYPE html>
<html lang="en">
<head>
<meta charset="utf-8">
<title>Delia Marsh – Makeup Artist Business Card</title>
<link rel="stylesheet" href="https://fonts.googleapis.com/css2?family=Libre+Baskerville:wght@400;700&display=swap">
<style>
  :root {
    --page-bg: #e9e7e8;
    --plum-deep: #2a0716;
    --plum: #5a1230;
    --berry: #a93d69;
    --rose: #c9567f;
    --name-pink: #ef4a82;
    --band-black: #120409;
    --skin-light: #efe0dc;
    --skin-mid: #cfaea8;
    --text-light: #ffffff;
  }
  * { margin: 0; padding: 0; box-sizing: border-box; }
  html, body {
    width: 1067px;
    height: 1200px;
    overflow: hidden;
    background: var(--page-bg);
    font-family: "Libre Baskerville", Georgia, serif;
  }
  .canvas { position: relative; width: 1067px; height: 1200px; }
  .card {
    position: absolute;
    left: 123px;
    width: 820px;
    height: 470px;
    border-radius: 30px;
    overflow: hidden;
    box-shadow: 0 10px 28px rgba(40, 10, 25, 0.28);
  }
  .card--front { top: 95px; }
  .card--back { top: 635px; }
  .card-art { position: absolute; inset: 0; width: 100%; height: 100%; display: block; }
  .identity {
    position: absolute;
    top: 30px;
    left: 26px;
    text-align: right;
  }
  .identity__name {
    color: var(--name-pink);
    font-weight: 700;
    font-size: 34px;
    line-height: 1.1;
  }
  .identity__role {
    color: var(--text-light);
    font-size: 22px;
    line-height: 1.3;
  }
  .contact {
    position: absolute;
    right: 24px;
    top: 330px;
    text-align: right;
    color: var(--text-light);
    font-size: 20px;
    line-height: 1.17;
  }
  .contact__line--strong { font-weight: 700; font-size: 18px; }
  .back-url {
    position: absolute;
    left: 0;
    right: 0;
    top: 372px;
    text-align: center;
    color: var(--text-light);
    font-weight: 700;
    font-size: 40px;
    letter-spacing: 0.5px;
  }
</style>
</head>
<body>
<main class="canvas">

  <section class="card card--front" aria-label="Business card front">
    <svg class="card-art" viewBox="0 0 820 470" preserveAspectRatio="none" aria-hidden="false">
      <defs>
        <linearGradient id="frontPhoto" x1="0" y1="0" x2="1" y2="0">
          <stop offset="0" stop-color="#2a0716"/>
          <stop offset="0.28" stop-color="#7a2350"/>
          <stop offset="0.5" stop-color="#6b4a55"/>
          <stop offset="0.72" stop-color="#cfaea8"/>
          <stop offset="1" stop-color="#efe0dc"/>
        </linearGradient>
        <linearGradient id="frontBand" x1="0" y1="0" x2="0" y2="1">
          <stop offset="0" stop-color="#c9567f"/>
          <stop offset="0.45" stop-color="#8e2a55"/>
          <stop offset="1" stop-color="#3d0b22"/>
        </linearGradient>
      </defs>
      <rect class="card-base" width="820" height="470" fill="url(#frontBand)"/>
      <polygon role="img" aria-label="Close-up photograph of a closed eye with smoky plum eyeshadow and a magenta hood"
               points="0,0 820,0 820,168 295,350 0,230" fill="url(#frontPhoto)"/>
      <polygon class="v-band" points="0,230 295,350 820,168 820,196 295,382 0,262" fill="var(--band-black)"/>
      <rect x="0" y="470" width="820" height="0" fill="none"/>
      <polygon class="band-sheen" points="0,262 295,382 820,196 820,300 0,330" fill="#ffffff" opacity="0.07"/>
    </svg>
    <div class="identity">
      <p class="identity__name">Delia Marsh</p>
      <p class="identity__role">Makeup Artist</p>
    </div>
    <div class="contact">
      <p class="contact__line">Phone USA: +1 (415)772-0461</p>
      <p class="contact__line">Singapore: +65 82307915: 0438 106 552</p>
      <p class="contact__line contact__line--strong">deliamarsh@moonveilstudio.net</p>
      <p class="contact__line contact__line--strong">www.moonveilstudio.net</p>
    </div>
  </section>

  <section class="card card--back" aria-label="Business card back">
    <svg class="card-art" viewBox="0 0 820 470" preserveAspectRatio="none">
      <defs>
        <linearGradient id="backPhoto" x1="0" y1="0" x2="1" y2="0">
          <stop offset="0" stop-color="#2a0716"/>
          <stop offset="0.3" stop-color="#a93d69"/>
          <stop offset="0.52" stop-color="#6b4a55"/>
          <stop offset="0.74" stop-color="#cfaea8"/>
          <stop offset="1" stop-color="#efe0dc"/>
        </linearGradient>
        <linearGradient id="backBand" x1="0" y1="0" x2="0" y2="1">
          <stop offset="0" stop-color="#c9567f"/>
          <stop offset="0.45" stop-color="#8e2a55"/>
          <stop offset="1" stop-color="#3d0b22"/>
        </linearGradient>
      </defs>
      <rect class="card-base" width="820" height="470" fill="url(#backBand)"/>
      <polygon role="img" aria-label="Close-up photograph of a closed eye with smoky plum eyeshadow and a magenta hood"
               points="0,0 820,0 820,168 295,350 0,230" fill="url(#backPhoto)"/>
      <polygon class="v-band" points="0,230 295,350 820,168 820,196 295,382 0,262" fill="var(--band-black)"/>
      <polygon class="band-sheen" points="0,262 295,382 820,196 820,300 0,330" fill="#ffffff" opacity="0.07"/>
    </svg>
    <p class="back-url">www.moonveilstudio.net</p>
  </section>

</main>
</body>
</html>
```